Residential Remodeling Contractor needs updated business card

I need a new design for my business card.
Name of the company is Ridgefell Construction. I need a card that commands presence, strength, integrity. I have been in business for 28 years. I am a Residential Remodeling Contractor that covers all aspects of a residential remodel and build.

```html
<!DOCTYPE html>
<html lang="en">
<head>
<meta charset="utf-8">
<title>Ridgefell Construction – Business Card</title>
<link rel="stylesheet" href="https://fonts.googleapis.com/css2?family=Montserrat:wght@400;500;600;800&display=swap">
<style>
  :root {
    --brand-blue: #1f3d7e;
    --brand-navy: #0f1f44;
    --band-grey: #dfe3ec;
    --ink: #1a1a1a;
    --paper: #ffffff;
    --backdrop: #e9eaec;
  }
  * { margin: 0; padding: 0; box-sizing: border-box; }
  html, body { width: 1200px; height: 900px; overflow: hidden; background: var(--backdrop); }
  body { font-family: "Montserrat", sans-serif; position: relative; }

  .card {
    position: absolute;
    left: 250px;
    width: 700px;
    height: 400px;
    overflow: hidden;
    box-shadow: 0 4px 14px rgba(0,0,0,0.18);
  }

  /* Back side */
  .card-back { top: 36px; background: var(--brand-blue); }
  .card-back .brand-lockup {
    position: absolute; left: 0; right: 0; top: 130px;
    display: flex; align-items: center; justify-content: center; gap: 16px;
  }
  .brand-mark-square { width: 22px; height: 22px; background: var(--brand-navy); }
  .card-back .brand-name {
    color: var(--brand-navy); font-weight: 800; font-size: 40px;
    letter-spacing: 2px; text-transform: uppercase; line-height: 1.05;
  }
  .tagline {
    position: absolute; left: 0; right: 0; bottom: 60px; text-align: center;
    color: var(--paper); font-weight: 600; font-size: 16px; letter-spacing: 2px;
    text-transform: uppercase;
  }

  /* Front side */
  .card-front { top: 464px; background: var(--paper); }
  .name-band {
    position: absolute; left: 0; top: 150px; width: 600px; height: 70px;
    background: var(--band-grey);
  }
  .person { position: absolute; left: 40px; top: 156px; }
  .person-name {
    color: var(--brand-blue); font-weight: 800; font-size: 28px; letter-spacing: 1px;
    text-transform: uppercase;
  }
  .person-title { color: var(--ink); font-size: 16px; font-weight: 400; margin-top: -2px; }

  .card-front .brand-lockup {
    position: absolute; right: 40px; top: 56px;
    display: flex; align-items: center; gap: 12px;
  }
  .card-front .brand-mark-square { background: var(--brand-blue); }
  .card-front .brand-name {
    color: var(--brand-blue); font-weight: 800; font-size: 30px;
    letter-spacing: 1.5px; text-transform: uppercase; line-height: 1.05;
  }

  .contact {
    position: absolute; left: 390px; top: 258px; color: var(--ink);
    font-size: 17px; font-weight: 500; line-height: 1.35;
  }
  .address { margin-bottom: 14px; }
  .contact-row { display: flex; align-items: center; gap: 8px; }
  .contact-row svg { width: 15px; height: 15px; flex: none; }
  .web-domain { color: var(--brand-blue); }
</style>
</head>
<body>

<section class="card card-back" aria-label="Business card back">
  <div class="brand-lockup">
    <span class="brand-mark-square"></span>
    <div class="brand-name">Ridgefell<br>Construction</div>
  </div>
  <p class="tagline">I have been in business for 28 years</p>
</section>

<section class="card card-front" aria-label="Business card front">
  <div class="brand-lockup">
    <span class="brand-mark-square"></span>
    <div class="brand-name">Ridgefell<br>Construction</div>
  </div>

  <div class="name-band"></div>
  <div class="person">
    <div class="person-name">Marcus Delane</div>
    <div class="person-title">Director</div>
  </div>

  <div class="contact">
    <p class="address">482 Harlow Street Athens,<br>GA 30605</p>
    <p class="contact-row">
      <svg viewBox="0 0 16 16" aria-hidden="true"><path d="M4 1.5l2.2 3-1.4 1.6c.8 1.8 2.3 3.3 4.1 4.1l1.6-1.4 3 2.2-1 2.5C7.4 13.3 2.7 8.6 1.5 2.5z" fill="var(--brand-blue)"/></svg>
      (555) 218-4470
    </p>
    <p class="contact-row">
      <svg viewBox="0 0 16 16" aria-hidden="true"><rect x="1.5" y="3.5" width="13" height="9" fill="none" stroke="var(--brand-blue)" stroke-width="1.4"/><path d="M1.5 3.5l6.5 5 6.5-5" fill="none" stroke="var(--brand-blue)" stroke-width="1.4"/></svg>
      info@ridgefellbuild.com
    </p>
    <p class="contact-row">
      <svg viewBox="0 0 16 16" aria-hidden="true"><g fill="none" stroke="var(--brand-blue)" stroke-width="1.3"><circle cx="8" cy="8" r="6.5"/><ellipse cx="8" cy="8" rx="3" ry="6.5"/><path d="M1.5 8h13M2.5 4.8h11M2.5 11.2h11"/></g></svg>
      <span>www.<span class="web-domain">ridgefellbuild</span>.com</span>
    </p>
  </div>
</section>

</body>
</html>
```